Business Card Design Project

We need a Business Card for an Mechanical Engineering firm in Singapore. The design should be Modern & Technical looking, yet eye catching.

Our company deals in Cutting Tools & Machine Accessories for the Manufacturing Industries such as Oil & Gas, Aero Space, etc... For more information on our Company, you can either email me or view our website www.torvalen.com.sg.

We are trying to revamp our image to give our consumers a fresh new perspective to our company, so we welcome all ideas.

Industry/Entity Type

Business

Requirements
Must have
• Must incorporate New Company Logo into the card as shown in Uploaded file.

```html
<!DOCTYPE html>
<html lang="en">
<head>
<meta charset="utf-8">
<title>Torvalen Tools – Business Card</title>
<link rel="stylesheet" href="https://fonts.googleapis.com/css2?family=Arimo:wght@400;700&family=Jost:wght@400;500&display=swap">
<style>
  :root {
    --bg: #ece8e6;
    --pink: #c97d90;
    --crimson: #9a1733;
    --paper: #f5f3f3;
    --rule: #ecd0d6;
    --white: #ffffff;
  }
  * { box-sizing: border-box; margin: 0; padding: 0; }
  html, body { width: 1200px; height: 900px; overflow: hidden; }
  body { background: var(--bg); position: relative; font-family: "Arimo", Arial, sans-serif; }

  .card {
    position: absolute; left: 250px; width: 700px; height: 400px;
    overflow: hidden; box-shadow: 0 6px 18px rgba(0,0,0,.18);
  }
  .card--front { top: 35px; }
  .card--back  { top: 465px; }
  .card__bg { position: absolute; inset: 0; width: 100%; height: 100%; }

  .brand {
    position: absolute; display: flex; align-items: center; gap: 10px;
    font-family: "Jost", sans-serif; font-weight: 500; color: var(--crimson);
    letter-spacing: 1px; white-space: nowrap; line-height: 1;
  }
  .brand__dot { border-radius: 50%; background: var(--crimson); flex: none; }
  .card--front .brand { left: 265px; top: 150px; font-size: 34px; }
  .card--front .brand__dot { width: 22px; height: 22px; }
  .card--back .brand  { left: 385px; top: 72px; font-size: 26px; }
  .card--back .brand__dot { width: 18px; height: 18px; }

  .front__web {
    position: absolute; left: 285px; top: 238px;
    font-family: "Jost", sans-serif; font-size: 17px; color: var(--crimson); letter-spacing: .5px;
  }

  .contact { position: absolute; left: 30px; color: var(--white); font-size: 15px; }
  .contact__row { display: flex; align-items: center; gap: 12px; height: 26px; }
  .contact__icon { width: 18px; height: 18px; flex: none; }
  .contact--phones { top: 140px; }
  .contact--address { top: 234px; }
  .contact--address .contact__row { align-items: flex-start; height: auto; }
  .contact--address .contact__icon { margin-top: 2px; }
  .address { line-height: 20px; font-size: 16px; }
  .address__company { font-weight: 700; }
  .contact--web { top: 320px; font-size: 16px; }

  .rule { position: absolute; height: 2px; background: var(--rule); }
  .rule--one { left: 0; top: 224px; width: 350px; }
  .rule--two { left: 0; top: 306px; width: 450px; }
  .rule--three { left: 560px; top: 230px; width: 140px; }

  .holder { position: absolute; left: 560px; top: 180px; color: var(--white); }
  .holder__name { font-size: 25px; font-weight: 700; letter-spacing: .5px; }
  .holder__role { font-size: 14px; margin-top: 2px; }
</style>
</head>
<body>

<section class="card card--front" aria-label="Card front">
  <svg class="card__bg" viewBox="0 0 700 400" aria-hidden="true">
    <rect width="700" height="400" fill="var(--pink)"/>
    <rect x="200" y="0" width="130" height="400" fill="var(--crimson)"/>
    <path d="M330 0 H700 V400 H260 C160 400 130 320 130 230 C130 100 200 0 330 0 Z" fill="var(--paper)"/>
  </svg>
  <div class="brand"><span class="brand__dot"></span>TORVALEN TOOLS</div>
  <p class="front__web">Website: info@torvalen.com.sg</p>
</section>

<section class="card card--back" aria-label="Card back">
  <svg class="card__bg" viewBox="0 0 700 400" aria-hidden="true">
    <rect width="700" height="400" fill="var(--pink)"/>
    <rect x="195" y="0" width="310" height="400" fill="var(--crimson)"/>
    <path d="M330 0 H700 V170 H375 Q330 170 330 125 Z" fill="var(--paper)"/>
  </svg>

  <div class="brand"><span class="brand__dot"></span>TORVALEN TOOLS</div>

  <div class="contact contact--phones">
    <div class="contact__row">
      <svg class="contact__icon" viewBox="0 0 20 20"><circle cx="10" cy="10" r="9" fill="#eee"/><path d="M7 5 l2 3 -1 1 q1 2 3 3 l1-1 3 2 -1 2 q-4 0 -7-4 t-1-5 z" fill="#888"/></svg>
      <span>Tel: 65-61234567</span>
    </div>
    <div class="contact__row">
      <svg class="contact__icon" viewBox="0 0 20 20"><circle cx="10" cy="10" r="9" fill="#eee"/><rect x="5" y="8" width="10" height="6" fill="#888"/><rect x="7" y="5" width="6" height="3" fill="#888"/></svg>
      <span>Fax: 65-61234568</span>
    </div>
    <div class="contact__row">
      <svg class="contact__icon" viewBox="0 0 20 20"><circle cx="10" cy="10" r="9" fill="#eee"/><rect x="5" y="6.5" width="10" height="7" fill="none" stroke="#888" stroke-width="1.4"/><path d="M5 6.5 l5 4 5-4" fill="none" stroke="#888" stroke-width="1.4"/></svg>
      <span>Email: info@torvalen.com.sg</span>
    </div>
  </div>

  <div class="rule rule--one"></div>

  <div class="contact contact--address">
    <div class="contact__row">
      <svg class="contact__icon" viewBox="0 0 20 20"><circle cx="10" cy="10" r="9" fill="#eee"/><path d="M5 10 l5-5 5 5 h-2 v4 h-6 v-4 z" fill="#888"/></svg>
      <p class="address">
        <span class="address__company">Torvalen Tools Pte Ltd</span><br>
        27 Kelvar Loop #03-08, Kelvar Business Hub,<br>
        Singapore 609581
      </p>
    </div>
  </div>

  <div class="rule rule--two"></div>

  <div class="contact contact--web">
    <div class="contact__row">
      <svg class="contact__icon" viewBox="0 0 20 20"><circle cx="10" cy="10" r="9" fill="#eee"/><circle cx="10" cy="10" r="5" fill="none" stroke="#888" stroke-width="1.4"/><path d="M5 10 h10 M10 5 v10" stroke="#888" stroke-width="1.2"/></svg>
      <span>Website: info@torvalen.com.sg</span>
    </div>
  </div>

  <div class="holder">
    <p class="holder__name">Marissa</p>
    <p class="holder__role">Designation</p>
  </div>
  <div class="rule rule--three"></div>
</section>

</body>
</html>
```